Business Card Design

I already have a company logo for my company. I have a logo for the manufacturer we represent. I want a professional business card design.

```html
<!DOCTYPE html>
<html lang="en">
<head>
<meta charset="utf-8">
<title>Business Card – Northgate Signal LLC</title>
<link href="https://fonts.googleapis.com/css2?family=Open+Sans:wght@400;600;700&display=swap" rel="stylesheet">
<style>
  :root {
    --stage: #232323;
    --card: #1e1e21;
    --card-shade: #19191b;
    --red: #e02326;
    --gold: #d9a22a;
    --text: #e4e4e4;
    --muted: #bdbdbd;
  }
  * { box-sizing: border-box; margin: 0; padding: 0; }
  html, body {
    width: 1200px; height: 780px; overflow: hidden;
    background: var(--stage);
    font-family: "Open Sans", Arial, sans-serif;
  }
  .stage {
    position: relative; width: 1200px; height: 780px;
    display: flex; align-items: center; justify-content: center; gap: 48px;
  }
  .card {
    position: relative; width: 520px; height: 297px;
    background: var(--card);
    border-radius: 3px;
    box-shadow: 0 14px 30px rgba(0,0,0,.55), 0 2px 4px rgba(0,0,0,.5);
    overflow: hidden;
  }
  /* front */
  .card-front::after {
    content: ""; position: absolute; top: 0; right: 0; width: 52%; height: 100%;
    background: linear-gradient(90deg, rgba(0,0,0,.28), rgba(0,0,0,0) 30%);
    pointer-events: none;
  }
  .identity { position: absolute; left: 60px; top: 58px; }
  .person-name { font-size: 27px; font-weight: 700; letter-spacing: .3px; line-height: 1.1; }
  .first-name { color: var(--red); }
  .last-name { color: var(--gold); }
  .person-title { margin-top: 6px; font-size: 14px; color: var(--muted); letter-spacing: .4px; padding-left: 48px; }
  .address { position: absolute; left: 60px; bottom: 48px; font-size: 14px; color: var(--text); letter-spacing: .3px; }
  .contact-list {
    position: absolute; left: 292px; top: 138px; list-style: none; z-index: 1;
    display: flex; flex-direction: column; gap: 6px;
  }
  .contact-item { display: flex; align-items: center; gap: 9px; font-size: 13.5px; color: var(--text); letter-spacing: .3px; }
  .contact-icon { width: 14px; height: 14px; flex: none; }
  /* back */
  .brand {
    position: absolute; right: 38px; bottom: 34px;
    display: flex; align-items: center; gap: 10px;
  }
  .brand-dot { width: 14px; height: 14px; border-radius: 50%; background: var(--red); }
  .brand-name { font-size: 20px; font-weight: 700; color: var(--text); letter-spacing: 1px; text-transform: uppercase; }
</style>
</head>
<body>
<main class="stage">
  <section class="card card-front" aria-label="Business card front">
    <div class="identity">
      <h1 class="person-name"><span class="first-name">Lena</span> <span class="last-name">Marovic</span></h1>
      <p class="person-title">Managing Director</p>
    </div>
    <ul class="contact-list">
      <li class="contact-item">
        <svg class="contact-icon" viewBox="0 0 24 24" aria-hidden="true"><path fill="#e02326" d="M6.6 10.8a15.1 15.1 0 0 0 6.6 6.6l2.2-2.2a1 1 0 0 1 1-.25 11.4 11.4 0 0 0 3.6.57 1 1 0 0 1 1 1V20a1 1 0 0 1-1 1A17 17 0 0 1 3 4a1 1 0 0 1 1-1h3.5a1 1 0 0 1 1 1c0 1.25.2 2.45.57 3.57a1 1 0 0 1-.25 1z"/></svg>
        (555) 014-2290
      </li>
      <li class="contact-item">
        <svg class="contact-icon" viewBox="0 0 24 24" aria-hidden="true"><rect x="2" y="5" width="20" height="14" rx="2" fill="#e02326"/><path d="M3 6l9 7 9-7" fill="none" stroke="#1e1e21" stroke-width="2"/></svg>
        hello@northgatesignal.com
      </li>
      <li class="contact-item">
        <svg class="contact-icon" viewBox="0 0 24 24" aria-hidden="true"><circle cx="12" cy="12" r="10" fill="#e02326"/><path d="M2 12h20M12 2c3 3 3 17 0 20M12 2c-3 3-3 17 0 20" fill="none" stroke="#1e1e21" stroke-width="1.6"/></svg>
        www.northgatesignal.com
      </li>
    </ul>
    <p class="address">1840 Alder Crest Rd. Suite 300 Denton, TX 76201</p>
  </section>

  <section class="card card-back" aria-label="Business card back">
    <div class="brand">
      <span class="brand-dot" aria-hidden="true"></span>
      <span class="brand-name">Northgate Signal LLC</span>
    </div>
  </section>
</main>
</body>
</html>
```